Advertising company unique advertising platform

we need a logo design for a new company based in Australia Melbourne. We develop innovated advertising platform where consumer can use this platform to get regular discount, as business owner they can use this platform for free advertisement. Payment for this advertisement platform only payable every two weeks, when I generate revenue for their business

Industry/Entity Type

Advertising

Contact Information for Business Card

Dale Morven | Co-Founder |Managing Director
Suite 718 240 Wattlebrook Lane Melbourne Vic 3000

ABN 38 614 207 923
Tel: +61 0487 259 318 | Email: dale.morven@plivorantu.com

Font styles to use
Decorative
Script

Requirements
Must have
• Try few different design and some round corner business card
Should not have
• One round corner business card...try 4 different colour background not only black, make sure two side is designed. Be creative so imagine you are giving this to a client make sure has wow factor, if you can also try one design with engrave like all the logo, words look 3d feel
• The word Advertising Platform use attached file font

```html
<!DOCTYPE html>
<html lang="en">
<head>
<meta charset="utf-8">
<title>Loomwell Market — Business Card</title>
<link rel="stylesheet" href="https://fonts.googleapis.com/css2?family=Roboto:wght@400;500;700&family=Roboto+Condensed:wght@700&display=swap">
<style>
  :root {
    --backdrop: #e9e6e1;
    --card: #2b2b2b;
    --name-red: #e8452c;
    --title-teal: #1fe0a8;
    --body-white: #f2f2f2;
    --brand-orange: #f47a3a;
    --divider: #6a6a6a;
    --band-teal: #2fc6c9;
    --band-blue: #3a7fd0;
    --band-orange: #ef6a2d;
    --band-yellow: #f3c43a;
    --faint-warm: rgba(214, 110, 50, 0.16);
  }
  * { box-sizing: border-box; margin: 0; padding: 0; }
  html, body { width: 1200px; height: 960px; overflow: hidden; }
  body {
    background: var(--backdrop);
    position: relative;
    font-family: "Roboto", Arial, sans-serif;
  }
  .card {
    position: absolute;
    background: var(--card);
    border-radius: 18px;
    box-shadow: 0 6px 14px rgba(0,0,0,0.35);
    overflow: hidden;
  }
  .card-front { left: 315px; top: 113px; width: 598px; height: 342px; }
  .card-back  { left: 312px; top: 473px; width: 599px; height: 340px; }

  .brand-mark {
    position: absolute;
    display: flex;
    align-items: center;
    gap: 12px;
  }
  .brand-dot {
    width: 40px; height: 40px;
    border-radius: 50%;
    background: var(--brand-orange);
    flex: none;
  }
  .brand-name {
    font-family: "Roboto", Arial, sans-serif;
    font-weight: 700;
    color: var(--brand-orange);
    line-height: 1.05;
  }
  .card-front .brand-mark { left: 48px; top: 146px; }
  .card-front .brand-name { font-size: 25px; }

  .divider {
    position: absolute;
    left: 303px; top: 56px;
    width: 2px; height: 252px;
    background: linear-gradient(to bottom, transparent, var(--divider) 20%, var(--divider) 80%, transparent);
  }
  .contact { position: absolute; left: 330px; top: 64px; color: var(--body-white); }
  .contact-name {
    font-family: "Roboto Condensed", "Arial Narrow", sans-serif;
    font-weight: 700;
    font-size: 20px; line-height: 24px; color: var(--name-red);
  }
  .contact-role {
    font-family: "Roboto", Arial, sans-serif;
    font-weight: 500;
    font-size: 14.5px; color: var(--title-teal); line-height: 19px; margin-top: 4px;
  }
  .contact-block { font-size: 14px; line-height: 18px; margin-top: 12px; }
  .contact-block.tight { margin-top: 8px; }
  .contact-line { display: flex; align-items: center; gap: 9px; line-height: 19px; }
  .contact-line svg { width: 13px; height: 13px; fill: var(--name-red); flex: none; }

  .edge-band { position: absolute; left: 0; bottom: 0; width: 100%; height: 10px; }
  .edge-band .cool { height: 4px; background: linear-gradient(to right, var(--band-teal), var(--band-blue)); }
  .edge-band .warm { height: 6px; background: linear-gradient(to right, var(--band-orange), var(--band-yellow), var(--band-orange)); }

  .back-accent {
    position: absolute;
    left: 370px; top: 60px;
    width: 200px; height: 200px;
    border-radius: 50%;
    background: var(--faint-warm);
  }
  .card-back .brand-mark { left: 62px; top: 186px; }
  .card-back .brand-name { font-size: 42px; }
  .website {
    position: absolute; left: 67px; top: 288px;
    font-size: 13px; letter-spacing: 2.6px; color: var(--body-white);
  }
</style>
</head>
<body>
  <section class="card card-front" aria-label="Business card front">
    <div class="brand-mark">
      <span class="brand-dot"></span>
      <span class="brand-name">Loomwell<br>Market</span>
    </div>
    <div class="divider"></div>
    <div class="contact">
      <div class="contact-name">DALE MORVEN</div>
      <div class="contact-role">CO-FOUNDER<br>MANAGING DIRECTOR</div>
      <div class="contact-block">Plivo Rantu<br>ABN 38 614 207 923</div>
      <div class="contact-block tight">Suite 718 240 Wattlebrook Lane<br>Melbourne Vic 3000</div>
      <div class="contact-block tight">
        <div class="contact-line">
          <svg viewBox="0 0 24 24"><path d="M6.6 10.8a15.1 15.1 0 0 0 6.6 6.6l2.2-2.2c.3-.3.7-.4 1-.2 1.1.4 2.3.6 3.6.6.6 0 1 .4 1 1V20c0 .6-.4 1-1 1A17 17 0 0 1 3 4c0-.6.4-1 1-1h3.5c.6 0 1 .4 1 1 0 1.3.2 2.5.6 3.6.1.3 0 .7-.2 1z"/></svg>
          <span>+61 0487 259 318</span>
        </div>
        <div class="contact-line">
          <svg viewBox="0 0 24 24"><path d="M2 5h20l-10 7.5z"/><path d="M2 7l10 7.5L22 7v12H2z"/></svg>
          <span>dale.morven@plivorantu.com</span>
        </div>
      </div>
    </div>
    <div class="edge-band"><div class="cool"></div><div class="warm"></div></div>
  </section>

  <section class="card card-back" aria-label="Business card back">
    <div class="back-accent" aria-hidden="true"></div>
    <div class="brand-mark">
      <span class="brand-name">Loomwell<br>Market</span>
    </div>
    <div class="website">www.plivorantu.com</div>
  </section>
</body>
</html>
```